Tallowmere Cornerstones

Need to improve polish and professionalism of PPT presentation. Get consistent look and feel through whole slides, improved look and feel while maintaining the corporate standards/colour scheme, from the Brackwyn corporate presentation. Need everything in Arial font with colours consistent with the PPT template

```html
<!DOCTYPE html>
<html lang="en">
<head>
<meta charset="utf-8">
<title>Tallowmere Cornerstones KPIs – Slide Set</title>
<link href="https://fonts.googleapis.com/css2?family=Arimo:wght@400;700&display=swap" rel="stylesheet">
<style>
  :root{
    --canvas:#d0d7da;
    --ink:#0c2530;
    --ink-mid:#1d4450;
    --body:#2b3a40;
    --red:#c9262d;
    --red-deep:#9c1e24;
    --teal:#1f7c97;
    --yellow:#efbd16;
    --yellow-deep:#e3a90c;
    --orange:#dc7a1d;
    --orange-deep:#c9661a;
    --white:#ffffff;
    --mist:#eceff0;
  }
  *{box-sizing:border-box;margin:0;padding:0}
  html,body{width:1017px;height:1200px;overflow:hidden}
  body{background:var(--canvas);font-family:"Arimo",Arial,sans-serif;color:var(--body);position:relative}

  .slide{position:absolute;width:482px;height:271px;background:var(--white);overflow:hidden;box-shadow:0 1px 3px rgba(0,0,0,.12)}
  .col-l{left:15.6px}.col-r{left:513.8px}
  .row-1{top:15px}.row-2{top:312px}.row-3{top:608px}.row-4{top:905px}

  .backdrop{position:absolute;right:0;top:0;width:62%;height:244px;
    background:linear-gradient(90deg,rgba(236,239,240,0) 0%,rgba(226,230,232,.7) 55%,#e1e5e7 100%)}

  .footer{position:absolute;left:0;bottom:0;width:100%;height:27px;background:var(--ink);color:var(--white)}
  .footer .legal{position:absolute;left:19.6px;top:10.5px;font-size:6px}
  .footer .brand{position:absolute;left:204px;top:7.5px;font-size:10px;font-weight:700;letter-spacing:.6px}
  .footer .page{position:absolute;right:20px;top:10px;font-size:6.3px;font-weight:700}

  .slide-title{position:absolute;left:19.6px;top:11px;font-size:19.6px;line-height:18.6px;font-weight:700;color:var(--ink)}

  .bullets{position:absolute;list-style:none;font-size:8.4px;line-height:11.6px}
  .bullets>li{position:relative;padding-left:17px;margin-bottom:3.4px}
  .bullets>li::before{content:"";position:absolute;left:0;top:1.6px;width:8px;height:8px;background:var(--red);
    clip-path:polygon(50% 0,61% 39%,100% 50%,61% 61%,50% 100%,39% 61%,0 50%,39% 39%)}
  .bullets .plain{padding-left:0}
  .bullets .plain::before{display:none}
  .ticks{list-style:none;margin:3px 0 1px}
  .ticks li{position:relative;padding-left:10px}
  .ticks li::before{content:"";position:absolute;left:0;top:2.6px;width:6px;height:6px;border-radius:50%;background:var(--red)}
  .ticks li::after{content:"";position:absolute;left:1.8px;top:3.7px;width:2.2px;height:1.2px;border-left:1px solid var(--white);border-bottom:1px solid var(--white);transform:rotate(-45deg)}
  .ticks.small{font-size:7.4px;line-height:12.1px;margin-left:17px}
  .ticks.small li{padding-left:14px}

  /* time usage model bars */
  .bar{position:absolute;display:flex;align-items:center;justify-content:center;color:var(--white);font-size:7.3px;border-radius:2px;text-align:center}
  .bar.dark{background:linear-gradient(90deg,var(--ink-mid),var(--ink))}
  .bar.teal{background:var(--teal)}
  .bar.red{background:linear-gradient(90deg,var(--red-deep),var(--red))}
  .bar.yellow{background:linear-gradient(180deg,var(--yellow),var(--yellow-deep))}
  .bar.orange{background:linear-gradient(180deg,var(--orange),var(--orange-deep))}

  /* production tree */
  .node{position:absolute;display:flex;align-items:center;justify-content:center;text-align:center;color:var(--white);
    font-weight:700;border-radius:4px;background:linear-gradient(90deg,var(--ink-mid),var(--ink));font-size:7.6px;line-height:11.4px}
  .node.root{left:295px;top:89px;width:116px;height:26px;font-size:8.8px}
  .node.left{left:245px;top:145px;width:98px;height:32px}
  .node.right{left:363px;top:145px;width:98px;height:32px}
  .node.hot{background:linear-gradient(90deg,var(--red-deep),var(--red))}
  .tree-lines{position:absolute;left:0;top:0}

  /* cover */
  .cover{background:var(--ink)}
  .cover .photo{position:absolute;left:0;top:0;width:145px;height:271px;
    background:linear-gradient(160deg,#b9a489 0%,#8a6f52 35%,#d8b23a 52%,#6a5440 75%,#4c3b2d 100%)}
  .cover .stripe{position:absolute;left:145px;top:0;width:17px;height:271px;background:linear-gradient(180deg,var(--red),var(--red-deep))}
  .cover .brand{position:absolute;left:189px;top:42px;color:var(--white);font-size:11.5px;font-weight:700;letter-spacing:.6px}
  .cover h1{position:absolute;left:189px;top:94px;color:var(--white);font-size:26px;line-height:26.5px;font-weight:700}
  .cover h1 .light{font-weight:400}
  .cover .date{position:absolute;left:189px;top:213px;color:var(--white);font-size:8px}
  .cover .legal{position:absolute;right:21px;top:255px;color:var(--white);font-size:6px}
</style>
</head>
<body>

<!-- Cover -->
<section class="slide cover col-l row-1">
  <div class="photo" role="img" aria-label="Yellow mining haul truck on a rocky pit floor"></div>
  <div class="stripe"></div>
  <div class="brand">BRACKWYN</div>
  <h1>Tallowmere<br>Cornerstones KPIs<br><span class="light">&amp; Production<br>Fundamentals</span></h1>
  <div class="date">13 November 2024</div>
  <div class="legal">2024 Brackwyn Mining Solutions Inc. Strictly Confidential</div>
</section>

<!-- Generic time usage model -->
<section class="slide col-r row-1">
  <div class="backdrop" role="img" aria-label="Faded line of haul trucks"></div>
  <h2 class="slide-title">Generic Time Usage Model</h2>
  <div class="bar dark" style="left:20px;top:41px;width:441px;height:17px">Calendat Time</div>
  <div class="bar dark" style="left:20px;top:59px;width:292px;height:18px">Available Time</div>
  <div class="bar red" style="left:313px;top:59px;width:148px;height:11px">Down</div>
  <div class="bar dark" style="left:20px;top:79.5px;width:145px;height:15px">Operating Time</div>
  <div class="bar dark" style="left:20px;top:96.5px;width:72px;height:15px">Effective Time</div>
  <div class="bar teal" style="left:94px;top:96.5px;width:71px;height:15px">Non-Effective Time</div>
  <div class="bar yellow" style="left:168px;top:79.5px;width:72px;height:32px">Operating Delay</div>
  <div class="bar orange" style="left:242px;top:79.5px;width:71px;height:32px">Standby Time</div>
  <div class="bar red" style="left:314px;top:71.5px;width:71px;height:40px">Unscheduled</div>
  <div class="bar red" style="left:387px;top:71.5px;width:74px;height:40px">Scheduled</div>
  <ul class="bullets" style="left:20px;top:132px;width:420px">
    <li>This is a generic Mining time usage model</li>
    <li>There may be variations from mine-to-mine (ie Utilized time vs Operating Time) but this model describes everything mine operations needs to know about the time usage of a piece of equipment</li>
  </ul>
  <footer class="footer"><span class="legal">2024 Brackwyn Mining Solutions Inc. Strictly Confidential</span><span class="brand">BRACKWYN</span><span class="page">05</span></footer>
</section>

<!-- KPI & production fundamentals -->
<section class="slide col-l row-2">
  <div class="backdrop" role="img" aria-label="Faded line of haul trucks"></div>
  <h2 class="slide-title">KPI &amp; Production<br>Fundamentals</h2>
  <ul class="bullets" style="left:20px;top:69px;width:228px">
    <li class="plain">At the end of this module, you will understand</li>
    <li>Understand the key concepts of mine production KPIs
      <ul class="ticks small" style="margin-left:0">
        <li>Time Usage Model</li>
        <li>Availability, Utilization and Productivity</li>
        <li>Elements of the haul cycle</li>
        <li>Elements of the loading cycle</li>
        <li>How changes in each of these elements impact mine production</li>
      </ul>
    </li>
  </ul>
  <ul class="bullets" style="left:241px;top:69px;width:200px">
    <li>The goal will be to create a baseline of under standing and a common language across the entire mine-ops team</li>
    <li>You may already understand these concepts</li>
    <li>This is the time to ask questions and get clarification!</li>
  </ul>
  <footer class="footer"><span class="legal">2024 Brackwyn Mining Solutions Inc. Strictly Confidential</span><span class="brand">BRACKWYN</span><span class="page">02</span></footer>
</section>

<!-- Calendar time -->
<section class="slide col-r row-2">
  <div class="backdrop" role="img" aria-label="Faded line of haul trucks"></div>
  <h2 class="slide-title">Generic Time Usage Model</h2>
  <div class="bar dark" style="left:20px;top:41px;width:441px;height:17px">Calendat Time</div>
  <ul class="bullets" style="left:20px;top:80px;width:420px">
    <li>Calendar time means all the time in a period
      <ul class="ticks">
        <li>Calendar time for 1 Year = 365 Days</li>
        <li>Calendar time for October = 31 days</li>
        <li>Calendar time for 1 shift = 12 hours</li>
      </ul>
    </li>
  </ul>
  <footer class="footer"><span class="legal">2024 Brackwyn Mining Solutions Inc. Strictly Confidential</span><span class="brand">BRACKWYN</span><span class="page">06</span></footer>
</section>

<!-- What makes up production 1 -->
<section class="slide col-l row-3">
  <div class="backdrop" role="img" aria-label="Faded line of haul trucks"></div>
  <h2 class="slide-title">What Makes up Production</h2>
  <ul class="bullets" style="left:20px;top:84px;width:222px">
    <li class="plain">In its simplest terms, we calculate production like this:</li>
    <li>This is true for any process
      <ul class="ticks small" style="margin-left:0">
        <li>Mowing the lawn</li>
        <li>Driving</li>
        <li>Mine Production</li>
      </ul>
    </li>
    <li style="margin-top:6px">Production goes up or down because of a change in Equipment Productivity or Operating Time</li>
  </ul>
  <svg class="tree-lines" width="482" height="271" aria-hidden="true"><path d="M348 115V129M315 129H391M315 129V145M391 129V145" stroke="#0c2530" stroke-width="1" fill="none"/></svg>
  <div class="node root">Products</div>
  <div class="node left">Equipment<br>Productivity</div>
  <div class="node right">Operating Time</div>
  <footer class="footer"><span class="legal">2024 Brackwyn Mining Solutions Inc. Strictly Confidential</span><span class="brand">BRACKWYN</span><span class="page">03</span></footer>
</section>

<!-- Available time -->
<section class="slide col-r row-3">
  <div class="backdrop" role="img" aria-label="Faded line of haul trucks"></div>
  <h2 class="slide-title">TUM – Available Time</h2>
  <div class="bar dark" style="left:20px;top:41.5px;width:441px;height:17px">Calendat Time</div>
  <div class="bar dark" style="left:20px;top:60px;width:292px;height:17px">Available Time</div>
  <div class="bar red" style="left:313px;top:60px;width:148px;height:10px">Down</div>
  <div class="bar red" style="left:314px;top:72.5px;width:71px;height:39.5px">Unscheduled</div>
  <div class="bar red" style="left:387px;top:72.5px;width:74px;height:39.5px">Scheduled</div>
  <ul class="bullets" style="left:20px;top:130px;width:430px">
    <li>Available Time is the time a piece of equipment (or fleet) is mechanically available to operate</li>
    <li>Available Time = Calendar Time – Down Time</li>
    <li>Downtime can be
      <ul class="ticks">
        <li>Planned (PMs, Rebuilds)</li>
        <li>Unplanned (Breakdown, Accident Damage)</li>
      </ul>
    </li>
    <li>Availability % = Available Time / Calendar Time</li>
  </ul>
  <footer class="footer"><span class="legal">2024 Brackwyn Mining Solutions Inc. Strictly Confidential</span><span class="brand">BRACKWYN</span><span class="page">05</span></footer>
</section>

<!-- What makes up production 2 -->
<section class="slide col-l row-4">
  <div class="backdrop" role="img" aria-label="Faded line of haul trucks"></div>
  <h2 class="slide-title">What Makes up Production</h2>
  <ul class="bullets" style="left:20px;top:66.5px;width:226px">
    <li class="plain">At its simplest terms, we calculate production like this:</li>
    <li>Operating time is the time when a piece of equipment is performing it’s primary function</li>
    <li>To better understand, communicate and discuss the different categories of how we calculate operating time, we use something called a <b>Time Usage Model</b></li>
    <li>Each industry has its own time usage model, and they can vary slightly from industry to industry</li>
    <li>Even within an industry, (e.g. Mining) a Time Usage Model can vary from operation to operation</li>
  </ul>
  <svg class="tree-lines" width="482" height="271" aria-hidden="true"><path d="M348 115V129M315 129H391M315 129V145M391 129V145" stroke="#0c2530" stroke-width="1" fill="none"/></svg>
  <div class="node root">Products</div>
  <div class="node left">Equipment<br>Productivity</div>
  <div class="node right hot">Operating Time</div>
  <footer class="footer"><span class="legal">2024 Brackwyn Mining Solutions Inc. Strictly Confidential</span><span class="brand">BRACKWYN</span><span class="page">04</span></footer>
</section>

<!-- Overview SIC -->
<section class="slide col-r row-4">
  <div class="backdrop" role="img" aria-label="Faded line of haul trucks"></div>
  <h2 class="slide-title">Overview – SIC &amp; Visual<br>Management</h2>
  <ul class="bullets" style="left:20px;top:70px;width:400px">
    <li>Dispatchers and Pit Supervisors use the SIC tool to monitor the real-time performance of the truck and shovel fleet.</li>
    <li>The tool is monitored hourly to identify underperformance. The dispatcher may be the lead in identi fying actions for the Pit Supervisor</li>
    <li>Once opportunities or underperforming areas are identified Dispatchers and Supervisors will take collaborative action to address them</li>
    <li>The Visual Management process is an accountability check and information share. ‘Did we monitor the SIC, communicate opportunities and take action during the shift?’</li>
  </ul>
  <footer class="footer"><span class="legal">2024 Brackwyn Mining Solutions Inc. Strictly Confidential</span><span class="brand">BRACKWYN</span><span class="page">08</span></footer>
</section>

</body>
</html>
```